New Electrical Business Card Design

I would like a new design for my business cards.
i would like the same logo and font but new design
Please see attached files for front and back design.
large image can be used for graphics.
I would like the instagram link incorporated to back of card.
website site address needs to be changed to www.kestrelhillelectrical.au
everything else stays as is

```html
<!DOCTYPE html>
<html lang="en">
<head>
<meta charset="utf-8">
<title>Kestrel Hill Electrical &amp; Data — Business Card</title>
<link rel="stylesheet" href="https://fonts.googleapis.com/css2?family=Poppins:wght@400;800&family=Oswald:wght@700&display=swap">
<style>
  :root {
    --backdrop: #2a2a2a;
    --green-dark: #036b33;
    --green: #04813f;
    --green-accent: #0c8a3e;
    --band: #050505;
    --paper-top: #f1f1f1;
    --paper-bottom: #e3e3e3;
    --ink: #111111;
    --text-grey: #3a3a3a;
    --band-text: #e9e9e9;
    --divider: #3bb3c9;
    --white: #f4f4f4;
  }
  * { box-sizing: border-box; margin: 0; padding: 0; }
  html, body { width: 1200px; height: 1138px; overflow: hidden; }
  body {
    background: var(--backdrop);
    font-family: "Poppins", sans-serif;
    position: relative;
  }
  .card {
    position: absolute;
    left: 288px;
    width: 624px;
    height: 376px;
    border-radius: 16px;
    overflow: hidden;
  }
  .card--front { top: 184px; background: linear-gradient(180deg, var(--green-dark) 0%, var(--green) 100%); }
  .card--back { top: 606px; background: linear-gradient(180deg, var(--paper-top) 0%, var(--paper-bottom) 100%); }

  .band {
    position: absolute;
    left: 0; right: 0; bottom: 0;
    height: 51px;
    background: var(--band);
    display: flex;
    align-items: center;
    justify-content: center;
    gap: 14px;
    color: var(--band-text);
    font-size: 16px;
    font-weight: 400;
  }
  .band__rule { width: 52px; height: 2px; background: linear-gradient(90deg, transparent, var(--green-accent), transparent); }
  .band__list { display: flex; align-items: center; }
  .band__sep { color: var(--green-accent); margin: 0 10px; }

  .wordmark { text-align: center; font-weight: 800; text-transform: uppercase; }
  .wordmark__name { display: block; line-height: 1; }
  .wordmark__tag { display: block; font-weight: 800; }

  .card--front .wordmark {
    position: absolute;
    left: 0; right: 0; top: 122px;
    color: var(--white);
  }
  .card--front .wordmark__name { font-size: 52px; letter-spacing: 0.01em; }
  .card--front .wordmark__tag { font-size: 18px; letter-spacing: 0.5em; margin-top: 10px; padding-left: 0.5em; }

  .card--back .wordmark {
    position: absolute;
    left: 30px; width: 250px; top: 146px;
    color: var(--ink);
  }
  .card--back .wordmark__name { font-size: 27px; }
  .card--back .wordmark__tag { font-size: 10px; letter-spacing: 0.45em; margin-top: 5px; padding-left: 0.45em; }

  .divider {
    position: absolute;
    left: 305px; top: 82px;
    width: 1px; height: 176px;
    background: var(--divider);
  }
  .contact { position: absolute; left: 339px; top: 100px; }
  .contact__name {
    font-family: "Oswald", sans-serif;
    font-weight: 700;
    font-size: 22px;
    letter-spacing: 0.01em;
    color: var(--ink);
    text-transform: uppercase;
    margin-bottom: 12px;
  }
  .contact__first { color: var(--green-accent); }
  .contact__list { list-style: none; }
  .contact__item {
    display: flex; align-items: center; gap: 12px;
    font-size: 15px; color: var(--text-grey);
    height: 22.5px;
  }
  .contact__icon { width: 15px; height: 15px; flex: none; }
  .contact__square { width: 13px; height: 13px; margin: 0 1px; border: 1.6px solid var(--green-accent); border-radius: 3px; flex: none; }
  .card--back .band { font-size: 15.5px; gap: 40px; }
</style>
</head>
<body>
  <section class="card card--front">
    <div class="wordmark">
      <span class="wordmark__name">Kestrel Hill</span>
      <span class="wordmark__tag">Electrical &amp; Data</span>
    </div>
    <div class="band">
      <span class="band__rule"></span>
      <p class="band__list">
        <span>Residential</span><span class="band__sep">|</span>
        <span>Commercial</span><span class="band__sep">|</span>
        <span>Industrial</span><span class="band__sep">|</span>
        <span>24hr Service</span>
      </p>
      <span class="band__rule"></span>
    </div>
  </section>

  <section class="card card--back">
    <div class="wordmark">
      <span class="wordmark__name">Kestrel Hill</span>
      <span class="wordmark__tag">Electrical &amp; Data</span>
    </div>
    <div class="divider"></div>
    <div class="contact">
      <h1 class="contact__name"><span class="contact__first">Daniel</span> Marrowby</h1>
      <ul class="contact__list">
        <li class="contact__item">
          <svg class="contact__icon" viewBox="0 0 16 16" fill="none" stroke="#0c8a3e" stroke-width="1.4"><circle cx="8" cy="8" r="6.8"/><path d="M5.6 4.8c.5-.4 1-.3 1.2.2l.5 1.2c.1.3 0 .6-.3.8l-.4.3c.4.9 1.1 1.6 2 2l.3-.4c.2-.3.5-.4.8-.3l1.2.5c.5.2.6.7.2 1.2-.6.8-1.6.9-2.6.3-1.3-.7-2.4-1.8-3.1-3.1-.5-1-.5-2 .2-2.7z" fill="#0c8a3e" stroke="none"/></svg>
          <span>0412 555 738</span>
        </li>
        <li class="contact__item">
          <svg class="contact__icon" viewBox="0 0 16 16" fill="none" stroke="#0c8a3e" stroke-width="1.4"><rect x="1.2" y="3.2" width="13.6" height="9.6" rx="1"/><path d="M1.6 3.8 8 9l6.4-5.2M1.6 12.4l4.6-4.6M14.4 12.4 9.8 7.8"/></svg>
          <span>info@kestrelhillelectrical.au</span>
        </li>
        <li class="contact__item">
          <svg class="contact__icon" viewBox="0 0 16 16" fill="none" stroke="#0c8a3e" stroke-width="1.3"><circle cx="8" cy="8" r="6.8"/><ellipse cx="8" cy="8" rx="3" ry="6.8"/><path d="M1.2 8h13.6M2.2 4.6h11.6M2.2 11.4h11.6"/></svg>
          <span>www.kestrelhillelectrical.au</span>
        </li>
        <li class="contact__item">
          <span class="contact__square"></span>
          <span>kestrel.hill.electrical</span>
        </li>
      </ul>
    </div>
    <div class="band">
      <span class="band__rule"></span>
      <p>ABN: 12 480 276 915 &nbsp;|&nbsp; LIC No.: 418062B</p>
      <span class="band__rule"></span>
    </div>
  </section>
</body>
</html>
```